Pre-Paid Card for Teens needs a design

We are a Fintech company called Toqavel. We will sell prepaid cards for families and teens. Now we need a prepaid card design. Prepaid card should have a orbitpay logo, company logo, 16 card number, expire date. Our webpage is http://www.toqavel-example.com
Target Market(s)
Teenages between 8 - 18 years old
Industry/Entity Type
It Company
Requirements
Must have
- The prepaid card must include toqavel logo, orbitpay debit card logo (I already attached a sample card), 16 digit card number and expire date.
Nice to have
- It should be fun and prestigious for young people.
Should not have
- We don't want that the card has a lots of color

```html
<!DOCTYPE html>
<html lang="en">
<head>
<meta charset="utf-8">
<title>Toqavel Prepaid Card</title>
<link rel="stylesheet" href="https://fonts.googleapis.com/css2?family=Comfortaa:wght@700&family=Share+Tech+Mono&family=Roboto:wght@700&display=swap">
<style>
  :root {
    --page-bg: #5a2410;
    --card-black: #040507;
    --brand-yellow: #fbbd1f;
    --brand-orange: #ee7b22;
    --brand-purple: #6a3596;
    --brand-deep-purple: #260a4a;
    --ink-white: #ffffff;
    --badge-silver-light: #d9dde2;
    --badge-silver-dark: #8b939c;
  }
  * { margin: 0; padding: 0; box-sizing: border-box; }
  html, body {
    width: 1200px;
    height: 1200px;
    overflow: hidden;
    background: var(--page-bg);
  }
  .card {
    position: absolute;
    left: 250px;
    top: 336px;
    width: 714px;
    height: 450px;
    border-radius: 16px;
    background: var(--card-black);
    overflow: hidden;
  }
  .brand {
    position: absolute;
    left: 36px;
    top: 36px;
    display: flex;
    align-items: center;
    gap: 24px;
  }
  .brand-dot {
    width: 84px;
    height: 84px;
    border-radius: 50%;
    background: var(--brand-purple);
  }
  .brand-name {
    font-family: "Comfortaa", sans-serif;
    font-weight: 700;
    font-size: 54px;
    line-height: 1;
    color: var(--brand-yellow);
    letter-spacing: 1px;
  }
  .decor-area {
    position: absolute;
    left: 0;
    top: 136px;
    width: 434px;
    height: 314px;
    border-top-right-radius: 150px;
    background: linear-gradient(90deg, var(--brand-yellow) 0%, var(--brand-orange) 70%, var(--brand-purple) 100%);
  }
  .card-number {
    position: absolute;
    left: 0;
    top: 244px;
    width: 100%;
    height: 40px;
    font-family: "Share Tech Mono", monospace;
    font-size: 36px;
    line-height: 40px;
    letter-spacing: 6px;
    color: var(--ink-white);
  }
  .digit-group {
    position: absolute;
    top: 0;
    white-space: nowrap;
  }
  .digit-group:nth-child(1) { left: 52px; }
  .digit-group:nth-child(2) { left: 180px; }
  .digit-group:nth-child(3) { left: 308px; }
  .digit-group:nth-child(4) { left: 436px; }
  .bin-digits {
    position: absolute;
    left: 53px;
    top: 298px;
    font-family: "Roboto", sans-serif;
    font-weight: 700;
    font-size: 13px;
    color: var(--ink-white);
  }
  .valid-label {
    position: absolute;
    left: 356px;
    top: 298px;
    font-family: "Roboto", sans-serif;
    font-weight: 700;
    font-size: 11px;
    line-height: 13px;
    color: var(--ink-white);
  }
  .expiry {
    position: absolute;
    left: 419px;
    top: 296px;
    font-family: "Share Tech Mono", monospace;
    font-size: 26px;
    line-height: 30px;
    letter-spacing: 5px;
    color: var(--ink-white);
  }
  .network-badge {
    position: absolute;
    left: 559px;
    top: 243px;
    width: 129px;
    height: 170px;
    border: 2px solid var(--ink-white);
    border-radius: 30px;
    display: flex;
    flex-direction: column;
    align-items: center;
    justify-content: space-between;
    padding: 10px 8px 16px;
  }
  .debit-seal {
    width: 110px;
    height: 70px;
    border-radius: 22px;
    background: linear-gradient(135deg, var(--badge-silver-light), var(--badge-silver-dark));
  }
  .network-name {
    display: flex;
    align-items: center;
    gap: 6px;
    font-family: "Roboto", sans-serif;
    font-weight: 700;
    font-size: 19px;
    color: var(--ink-white);
  }
  .network-dot {
    width: 16px;
    height: 16px;
    border-radius: 50%;
    background: var(--brand-orange);
  }
</style>
</head>
<body>
  <div class="card">
    <div class="decor-area" role="img" aria-label="Large brand graphic in yellow, orange and purple"></div>

    <div class="brand">
      <span class="brand-dot"></span>
      <span class="brand-name">toqavel</span>
    </div>

    <div class="card-number">
      <span class="digit-group">5157</span>
      <span class="digit-group">5500</span>
      <span class="digit-group">0000</span>
      <span class="digit-group">0000</span>
    </div>
    <div class="bin-digits">5157</div>
    <div class="valid-label">VALID<br>THRU</div>
    <div class="expiry">10/20</div>

    <div class="network-badge">
      <div class="debit-seal" role="img" aria-label="Debit security seal"></div>
      <div class="network-name"><span class="network-dot"></span>orbitpay</div>
    </div>
  </div>
</body>
</html>
```